ORIM Holding

ORIM holding is located in the UAE. In the company, there are several departments covering Hospitality management, Facility Management, interior design and Construction.

The logo should not include the name holding, Just ORIM.

Needed Items:

(1) Logo.
(2) Business Card.
(3) Letterhead
(4) Envelope
(5) cd cover
(6) email signature
Updates

The previous brief was misplaced with another competition. Current update is the final.

Target Market(s)

Collaboration with international high end firms.

Industry/Entity Type

Business

Requirements
Must have
• COLOR PREFERENCE Maximum 2 colors, preferably mono-color with different shades.
Nice to have
• Elegant, luxurious, and minimalistic.

```html
<!DOCTYPE html>
<html lang="en">
<head>
<meta charset="UTF-8">
<title>ORIM Holding – Business Card</title>
<link rel="stylesheet" href="https://fonts.googleapis.com/css2?family=Montserrat:wght@500;600;700&family=Arimo:wght@400&display=swap">
<style>
  :root {
    --backdrop: #c8c8c8;
    --orange: #f26722;
    --orange-deep: #d95a1c;
    --ink: #2f2f2f;
    --paper: #ffffff;
    --ghost: #ececec;
  }
  * { box-sizing: border-box; margin: 0; padding: 0; }
  html, body { width: 1200px; height: 900px; overflow: hidden; }
  body {
    background: var(--backdrop);
    font-family: "Arimo", Arial, sans-serif;
    position: relative;
  }
  .card {
    position: absolute;
    width: 680px;
    height: 390px;
    left: 260px;
    border-radius: 28px;
    overflow: hidden;
    box-shadow: 0 6px 14px rgba(0,0,0,0.18);
  }
  .card--back { top: 35px; background: var(--orange); }
  .card--front { top: 475px; background: var(--paper); }

  .wordmark {
    position: absolute;
    font-family: "Montserrat", Arial, sans-serif;
    font-weight: 700;
    letter-spacing: 0.04em;
    line-height: 1;
    white-space: nowrap;
  }
  .brand-dot {
    position: absolute;
    border-radius: 50%;
  }

  /* Back side */
  .card--back .wordmark--ghost {
    color: var(--orange-deep);
    font-size: 150px;
    right: -30px;
    top: 10px;
  }
  .card--back .wordmark--main {
    color: var(--paper);
    font-size: 92px;
    left: 50%;
    top: 50%;
    transform: translate(-42%, -50%);
  }
  .card--back .brand-dot {
    width: 34px; height: 34px;
    background: var(--paper);
    left: 170px; top: 178px;
  }

  /* Front side */
  .card--front .wordmark--ghost {
    color: var(--ghost);
    font-size: 150px;
    right: -30px;
    top: 20px;
  }
  .card--front .wordmark--main {
    color: var(--orange);
    font-size: 62px;
    left: 92px;
    top: 78px;
  }
  .card--front .brand-dot {
    width: 24px; height: 24px;
    background: var(--ink);
    left: 56px; top: 98px;
  }
  .person {
    position: absolute;
    left: 70px;
    top: 196px;
  }
  .person__name {
    font-family: "Montserrat", Arial, sans-serif;
    font-weight: 600;
    font-size: 27px;
    color: var(--orange);
    letter-spacing: 0.02em;
    text-transform: uppercase;
  }
  .person__role {
    font-size: 18px;
    color: var(--ink);
    margin-top: 2px;
  }
  .contacts {
    position: absolute;
    left: 70px;
    top: 272px;
    list-style: none;
  }
  .contacts li {
    display: flex;
    align-items: center;
    gap: 10px;
    font-size: 18px;
    color: var(--ink);
    height: 30px;
  }
  .contacts svg { width: 18px; height: 18px; flex: none; }
  .address {
    position: absolute;
    right: 48px;
    top: 230px;
    text-align: right;
    font-size: 18px;
    line-height: 1.3;
    color: var(--ink);
  }
</style>
</head>
<body>

<section class="card card--back" aria-label="Business card, back">
  <span class="wordmark wordmark--ghost" aria-hidden="true">ORIM</span>
  <span class="brand-dot"></span>
  <span class="wordmark wordmark--main">ORIM</span>
</section>

<section class="card card--front" aria-label="Business card, front">
  <span class="wordmark wordmark--ghost" aria-hidden="true">ORIM</span>
  <span class="brand-dot"></span>
  <span class="wordmark wordmark--main">ORIM</span>

  <div class="person">
    <p class="person__name">Daniel Reeves</p>
    <p class="person__role">Managing Director</p>
  </div>

  <ul class="contacts">
    <li>
      <svg viewBox="0 0 24 24" aria-hidden="true"><path fill="var(--orange)" d="M6.6 10.8a15.1 15.1 0 0 0 6.6 6.6l2.2-2.2a1 1 0 0 1 1-.25 11.4 11.4 0 0 0 3.6.57 1 1 0 0 1 1 1V20a1 1 0 0 1-1 1A17 17 0 0 1 3 4a1 1 0 0 1 1-1h3.5a1 1 0 0 1 1 1c0 1.25.2 2.45.57 3.57a1 1 0 0 1-.25 1z"/></svg>
      044-555 010 200
    </li>
    <li>
      <svg viewBox="0 0 24 24" aria-hidden="true"><rect x="2" y="5" width="20" height="14" rx="1.5" fill="var(--orange)"/><path d="M3 6.5l9 6.5 9-6.5" fill="none" stroke="#fff" stroke-width="1.6"/></svg>
      info@orimmail.com
    </li>
    <li>
      <svg viewBox="0 0 24 24" aria-hidden="true"><g fill="none" stroke="var(--orange)" stroke-width="1.8"><circle cx="12" cy="12" r="9.5"/><ellipse cx="12" cy="12" rx="4.2" ry="9.5"/><path d="M2.5 12h19M4 7h16M4 17h16"/></g></svg>
      www.orimholding.com
    </li>
  </ul>

  <address class="address" style="font-style:normal">
    421 , Address line goes here<br>
    45452,Country Name
  </address>
</section>

</body>
</html>
```